New business card/stationary for a consulting company

I am looking for a clean and very professional looking business card for my consulting company as well as corresponding stationary. I am uploading our logo. I like simple and powerful for the feel. No graphics but I am open on everything else. Below is my contact information but would like the final to be in a version I can add my employees information into and print. Thank you.

Daniel Whitcombe
dan@ferncliffadvisory.com
2870 North 9th Avenue, Summit Floor, Elm Ridge, Illinois 60531
www.ferncliffadvisory.com

Industry/Entity Type

Consulting

Contact Information for Business Card

Daniel Whitcombe
dan@ferncliffadvisory.com
www.ferncliffadvisory.com

Font styles to use
Serif
Sans Serif

Requirements
Must have
• Our logo and the business card details.
Nice to have
• our website www.ferncliffadvisory.com

```html
<!DOCTYPE html>
<html lang="en">
<head>
<meta charset="utf-8">
<title>Ferncliff Advisory – Business Card</title>
<link rel="stylesheet" href="https://fonts.googleapis.com/css2?family=Marcellus&family=Roboto:wght@400&display=swap">
<style>
  :root {
    --navy: #132c5c;
    --paper: #f7f7f7;
    --backdrop: #e4e4e4;
    --ink: #2b2b2b;
    --white: #ffffff;
  }
  * { margin: 0; padding: 0; box-sizing: border-box; }
  html, body {
    width: 1200px;
    height: 576px;
    overflow: hidden;
    background: var(--backdrop);
  }
  .canvas {
    position: relative;
    width: 1200px;
    height: 576px;
  }
  .card {
    position: absolute;
    border-radius: 13px;
  }
  .card--front {
    left: 82px; top: 139px;
    width: 484px; height: 292px;
    background: var(--navy);
    color: var(--white);
    display: flex;
    flex-direction: column;
    align-items: center;
    justify-content: center;
  }
  .card--back {
    left: 602px; top: 138px;
    width: 481px; height: 291px;
    background: var(--paper);
  }
  .brand-square {
    width: 26px; height: 26px;
    background: var(--white);
    margin-bottom: 18px;
  }
  .brand-name {
    font-family: "Marcellus", serif;
    font-size: 24px;
    letter-spacing: 1.5px;
    text-transform: uppercase;
    margin-top: 0;
  }
  .back-brand {
    position: absolute;
    left: 38px; top: 104px;
    width: 174px;
    color: var(--navy);
  }
  .back-brand .brand-square {
    background: var(--navy);
    width: 24px; height: 24px;
    margin-bottom: 12px;
  }
  .back-brand .brand-name {
    font-size: 20px;
    line-height: 1.2;
    letter-spacing: 1.2px;
  }
  .contact {
    position: absolute;
    left: 249px; top: 91px;
    font-family: "Roboto", sans-serif;
    color: var(--ink);
  }
  .contact__name {
    font-family: "Marcellus", serif;
    font-size: 17px;
    color: var(--navy);
    letter-spacing: 1px;
    text-transform: uppercase;
    margin-bottom: 6px;
  }
  .contact__line {
    display: flex;
    align-items: center;
    font-size: 12.5px;
    height: 19px;
  }
  .contact__line svg {
    width: 10px; height: 10px;
    margin-right: 10px;
    fill: var(--navy);
  }
  .contact__address {
    margin-top: 7px;
    font-size: 12.5px;
    line-height: 19px;
  }
</style>
</head>
<body>
<main class="canvas">
  <section class="card card--front" aria-label="Card front">
    <div class="brand-square"></div>
    <p class="brand-name">Ferncliff Advisory</p>
  </section>

  <section class="card card--back" aria-label="Card back">
    <div class="back-brand">
      <div class="brand-square"></div>
      <p class="brand-name">Ferncliff<br>Advisory</p>
    </div>
    <div class="contact">
      <p class="contact__name">Daniel Whitcombe</p>
      <p class="contact__line">
        <svg viewBox="0 0 10 10" aria-hidden="true"><path d="M0 2h10v6H0z"/><path d="M0 2l5 3.5L10 2" fill="none" stroke="#f7f7f7" stroke-width="0.9"/></svg>
        dan@ferncliffadvisory.com
      </p>
      <p class="contact__line">
        <svg viewBox="0 0 10 10" aria-hidden="true"><circle cx="5" cy="5" r="4.5"/><path d="M0.5 5h9M5 0.5v9M5 0.5c-2.4 2.6-2.4 6.4 0 9M5 0.5c2.4 2.6 2.4 6.4 0 9" fill="none" stroke="#f7f7f7" stroke-width="0.6"/></svg>
        www.ferncliffadvisory.com
      </p>
      <p class="contact__address">2870 North 9th Avenue, Summit<br>Floor, Elm Ridge, Illinois 60531</p>
    </div>
  </section>
</main>
</body>
</html>
```